Corvex Hiring Partners Business Cards

Business cards with logo design for a new recruiting company called "Corvex Hiring Partners"

incorporate RED & BLUE colors

Final design should reflect strength - clean, elegant design

Company name superimposed upon graphic (Greek Columns)

Please see attached Photos!!!

Industry/Entity Type

Business

Font styles to use
Decorative

Colors
ec2027
0555a3
85cae6

Requirements
Must have
• Must look very similar to attached design!!!

Want Company name superimposed upon graphic (Greek Columns)

Tag line at bottom must be included:
"Empowering Exceptional Companies with Exceptional People"

```html
<!DOCTYPE html>
<html lang="en">
<head>
<meta charset="utf-8">
<title>Corvex Hiring Partners – Business Card</title>
<link rel="stylesheet" href="https://fonts.googleapis.com/css2?family=Lato:wght@400;700&display=swap">
<style>
  :root {
    --page-bg: #6b6b6b;
    --card-white: #ffffff;
    --brand-red: #ec2027;
    --brand-blue: #0555a3;
    --mark-tone: #e3e4e6;
    --text-white: #ffffff;
  }
  * { box-sizing: border-box; margin: 0; padding: 0; }
  html, body {
    width: 1200px;
    height: 900px;
    overflow: hidden;
    background: var(--page-bg);
    font-family: "Lato", sans-serif;
  }
  .business-card {
    position: absolute;
    left: 75px;
    top: 150px;
    width: 1050px;
    height: 600px;
    background: var(--card-white);
    overflow: hidden;
  }
  .brand-block {
    position: absolute;
    left: 0;
    top: 0;
    width: 100%;
    height: 372px;
  }
  .brand-square {
    position: absolute;
    left: 395px;
    top: 112px;
    width: 260px;
    height: 260px;
    background: var(--mark-tone);
  }
  .brand-name {
    position: absolute;
    left: 0;
    top: 150px;
    width: 100%;
    color: var(--brand-blue);
    font-weight: 700;
    font-size: 46px;
    line-height: 1.2;
    text-align: center;
  }
  .name-band {
    position: absolute;
    left: 0;
    top: 372px;
    width: 100%;
    height: 66px;
    background: var(--brand-red);
    display: flex;
    align-items: center;
    justify-content: space-between;
    padding: 0 44px 0 56px;
    color: var(--text-white);
  }
  .person-name {
    font-size: 42px;
    font-weight: 400;
  }
  .person-name .initial { font-weight: 700; }
  .phone { font-size: 25px; }
  .phone .label { font-weight: 700; }
  .contact-band {
    position: absolute;
    left: 0;
    top: 438px;
    width: 100%;
    height: 162px;
    background: var(--brand-blue);
    color: var(--text-white);
    text-align: center;
  }
  .contact-line {
    margin-top: 26px;
    font-size: 24px;
    display: flex;
    justify-content: center;
    gap: 26px;
  }
  .contact-line .label { font-weight: 700; }
  .divider { opacity: 0.9; }
  .tagline {
    margin-top: 34px;
    font-size: 31px;
    font-weight: 700;
    letter-spacing: 0.3px;
  }
</style>
</head>
<body>
  <main class="business-card">
    <section class="brand-block">
      <div class="brand-square" role="img" aria-label="Brand mark area: company name set over a pair of classical columns"></div>
      <h1 class="brand-name">Corvex<br>Hiring<br>Partners</h1>
    </section>

    <section class="name-band">
      <p class="person-name">Daniel <span class="initial">R</span> Whitcombe</p>
      <p class="phone"><span class="label">phone</span>: 512 555 010</p>
    </section>

    <section class="contact-band">
      <p class="contact-line">
        <span><span class="label">web:</span> www.CorvexHP.com</span>
        <span class="divider">|</span>
        <span><span class="label">email:</span> DWhitcombe@CorvexHP.com</span>
      </p>
      <p class="tagline">Empowering Exceptional Companies with Exceptional People</p>
    </section>
  </main>
</body>
</html>
```